Brochure Brightwell Hearth Partners

Brochure 12 x 9 tri fold with insert/ Rack card 9x4. Brightwell Hearth Partners 318 Corvane Street Easton, MD 21629410-822-2207AgingAtHomeSolution.com Tag: Devoted to Thoughtful Household Support.
What we do: Home care agency that services higher end Clients Artsy area on the water. Taking care of seniors in their home.

Our story: Opening Brightwell Hearth Partners, Inc. is my way of making a difference in an industry that is dominated by franchises that often have their policies dictated by corporate policy-makers who are unfamiliar with local customs. My goal is to raise the level of non-medical home health care in our area by providing additional, customized training, higher wages for our care-partners and an inclusive workforce in the decision-making process when developing customized care planning for our clients. Through collaboration with the client, their family and care-partners I have learned what issues, concerns and disappointments may arise which enables me to provide a more defined solution for those in need.My goal of providing superior training required locating a nationally recognized curriculum that would serve our clients’ needs. I found the perfect fit with Norla Vance’s, Kindred Pathway Method™ and her Shifting Stones Series™. These programs provide our care-partners with the tools needed to handle the challenges of natural aging and living with Dementia. I was so impressed with these programs, I became a Certified Independent Trainer; one of five in the State of Maryland. There is a bonus for our care-partners who are required to maintain Continuing Education Units - these programs qualify for credit! Improving our industry by providing exemplary care-partners is my goal!I look forward to assisting you with your needs! Dana Prewitt Owner

Services: Companion Care Service - Conversation and Companionship , Meal Preparation, Light House Keeping, Errand Service ,Grocery Shopping ,Incidental Transportation, Laundry & Linen Washing, Medication Reminders, Recreational Activities ,
Personal Care Services: Bathing ,Mobility ,Transferring & Positioning ,Incontinence Care ,Oral Hygiene ,Feeding, Toileting ,Grooming & Dressing, Special Diet Preparation.

Our Commitment to You: Extensive Care-Partner Education - We provide, in addition to state mandated training, eight additional hours of hands-on Dementia training from a Certified, Independent Instructor on the “Kindred Pathway Method” by Norla Vance, a nationally recognized instructor on aging.

Nutrition/Local Chef Inspired Training ;We provide six, two-hour food preparation sessions for our care-partners using local chefs, their recipes and locally grown food.

Meaningful & Engaging Activities - We provide a monthly list with local activities to our care-partners based on our client’s interest and capabilities. Focusing on what our client loved to do in the past.

Home Solutions When Needed; We provide management services to help keep our clients in their homes by working with current contractors or locating new ones to properly maintain a safe-living environment.

About owner: Dana Prewitt, owner of Brightwell Hearth Partners, has earned her certification as an Independent Trainer in the Kindred Pathway; Method (KPM) by Norla Vance, a nationally recognized instructor on natural aging and aging with Dementia. Dana is one of five certified independent trainers in the state of Maryland. All staff will have eight hours of hands on Dementia Kindred Pathway Method training.

On the insert 11x 4.25 want the top to be sticking out of the tri -fold "Dementia Experts . I would like to have shades of each STONE as it progresses
The Shifting STONES(R): The STONES model recognizes the dynamic nature of the human brain and its abilities. Unlike other cognitive models, it acknowledges that everyone’s abilities can change in a moment. Modifying environments, situations, interactions, and expectations will create either supportive positive opportunities or result in distress and a sense of failure. Just as gemstones need different settings and care to show their best characteristics, so do people. Rather than focusing on a person’s loss when there is brain change, seeing individuals as precious, unique, and capable encourages a care partnership and is the core of this model. Providing supportive settings for everyone, including care providers, allows them to use what they have to be their best. The STONES® advocate that everyone living with brain change when given the opportunity will shine. Norla Vance and Kindred Pathway Method

Sapphire ~ True Blue ~ Optimal Cognition, Healthy Brain•
True to self: personal preferences remain basically the same
• Can be flexible in thinking and appreciate multiple perspectives
• Stress/pain/fatigue may trigger Diamond state: back to Sapphire with relief
• Able to suppress and filter personal reactions: chooses effective responses
• Selects from options and can make informed decisions
• Processes well and able to successfully transition
• Aging doesn’t change ability: processing slows, more effort/time/practice needed
My brain is healthy - true blue. If I am aging normally or distressed, it may be hard for me to find words. I can describe what I am thinking so you understand. I may talk to myself because I am giving myself cues and prompts. I can learn new things and change habits, but it takes time and effort. Honoring my choices and preferences, when possible, is important. I need more time to make decisions. Give me the details and let me think about it before you need an answer. I am able to remember plans and information but supports are helpful. I may like specific prompts such as notes, calendars, and reminder calls. Health changes in vision, hearing, balance, coordination, depression, anxiety, pain, or medication may impact my behavior, but my cognitive abilities remain the same.

Diamond ~ Clear and Sharp ~ Routines and Rituals Rule
• Displays many facets: behavior and perspective can shift dramatically
• Prefers the familiar and may resist change: challenged by transitions
• More rigid and self-focused; sees wants as needs, when stressed
• Personal likes/dislikes in relationships/space/belongings etc, become more intense
• Reacts to changes in environment; benefits from familiar; functional/forgiving
• Needs repetition and time to absorb new/different information or routines
• Trusted authority figures can help: reacts better when respect is mutual
My overall cognition is clear and sharp. When happy and supported, I am capable and shine in my abilities. When distressed, I can be cutting and rigid and may see help as a threat. I have trouble seeing other points of view and may become less aware of boundaries or more possessive about my relationships, personal space, and belongings. I have many facets so people see me differently depending on the situation. This can cause conflict among my family, friends, or care team as it’s hard to tell if I am choosing my behavior or truly have limits in my ability. I can socially engage and have good cover skills. People will vary in their awareness of what is happening to me. I want to keep habits and environments as they have always been, even if they are problematic for me or others. I am often focused on the past, personal values, or finances. I will need help to make changes in my life; it’s hard for me. I can be in a Diamond state for reasons other than dementia.

Emerald ~ Green and On the Go With a Purpose ~ Naturally Flawed
• Sees self as able and independent, with limited awareness of changes in ability
• Lives in moments of clarity mixed with periods of loss in logic/reason/perspective
• Understanding and use of language change: vague words and many repeats
• Cues and support help when getting to/from places and doing daily routines
• Awareness of time, place, and situation will not always match current reality
• Strong emotional reactions are triggered by fears, desires, or unmet needs
Needs to know what comes next: seeks guidance and assistance to fill the day
I am flawed; it is part of being a natural emerald. I tend to be focused on what I want or need in this moment and may not be aware of my own safety or changing abilities. I can chat socially, but I typically miss one out of every four words and cannot accurately follow the meaning of longer conversations. I won’t remember the details of our time together, but I will remember how your body language and tone of voice made me feel. I may hide or misplace things and believe someone has taken them. My brain will make up information to fill in the blanks, which makes you think I am lying. If you try to correct me or argue, I may become resentful or suspicious of you. I am not always rational, but I don’t want to be made to feel incompetent. My brain plays tricks on me, taking me to different times and places in my life. When I am struggling, I may tell you, “I want to go home.” To provide the help and assistance I need, you must go with my flow, use a positive, partnered approach, and modify my environment.

Amber ~ Caught in a Moment of Time ~ Caution Required
• Focused on sensation: seeks to satisfy desires and tries to avoid what is disliked
•Environment can drive actions and reactions without awareness of safety
• Visual abilities are limited: focus is on pieces or parts, not the whole picture
• What happens to or around an Amber, may cause strong and surprising reactions
• Enters others’ space and crosses boundaries attempting to meet own needs
• Has periods of intense activity: may be very curious or repetitive with objects or actions
• Care is refused or seen as threatening, due to differences in perspective and ability.
Like a particle trapped in an amber, I am caught in a moment of time. It may surprise you to see how I take in the world around me. I may not know you or see you as a whole person. I react to you based on how you look, sound, move, smell, and respond to me. I like to do simple tasks over and over and may need to repeatedly move and touch, smell, taste, take or tear items apart. While it may exhaust or frustrate you, it soothes me. I don’t recognize danger; you will have to safeguard my environment. I’m intolerant to discomfort because my mouth, hands, feet, and genitalia are highly sensitive due to changes in my nervous system. Therefore, activities like eating, taking medication, mouth care, bathing, dressing, and toileting may distress me. Please notice my reaction and stop if I am resisting. I can’t help myself and one or both of us may get hurt emotionally and/or physically. If this happens, wait a few minutes, connect with me, and try a different approach; possibly substituting one area of focus for another.

Ruby ~ Deep and Strong in Color ~ Others Stop Seeing What is Possible
• Makes use of rhythm: can usually sing, hum, pray, sway, rock, clap, and dance
• When moving can’t stop; when stopped can’t get moving: needs guidance and help
• Big, strong movements are possible, while skilled abilities are being lost
• Danger exists due to limited abilities combined with automatic actions or reactions
• Tends to miss subtle hints, but gets magnified facial expressions and voice rhythms
• Can mimic actions or motions, but will struggle to understand instructions/gestures
• Able to pick up and hold objects, and yet not know what to do with them
As the deep red of a ruby masks detail, my obvious losses make my remaining abilities harder to notice. Although my fine motor skills have become very limited, remember that I am able to move and do simple things with my hands. You will need to anticipate, identify, and respond to all of my needs, even though I may not be aware of them. Plan to create a supportive environment, help with the details of care, and structure my day. Just as a crossing guard directs traffic, you will need to guide my movements and transitions. I can rarely stop or start on my own and switching gears is a challenge. Move with me first, then use your body to show me what you want me to do next, going one step at a time. Palm-beneath-Palm™ assistance helps me to feel safe and secure and to know what to do. Danger is part of my life, due to losses in visual skills, chewing abilities, balance, and coordination. You can reduce the risks to me, but not eliminate them. I can still have moments of joy when you are able to provide what gives me pleasure.

Pearl ~ Hidden Within a Shell ~ Beautiful Moments to Behold
• Will frequently recognize familiar touches, voices, faces, aromas, and tastes• Personhood survives, although all other capabilities are minimal
• Understanding input takes time: go slow and simplify for success
• In care, first get connected by offering comfort then use careful and caring touch
• Changes in the body are profound: weight loss, immobility, systems are failing
• As protective reflexes are lost, breathing, swallowing, and moving will be difficult
Care partners benefit from learning the art of letting go rather than simply giving up
While hidden like a pearl in an oyster shell, I will still have moments when I become alert and responsive. I am near the end of my life. Moments of connection create a sense of wholeness and value between us. Use our time together not just to provide care, but to comfort and connect with me. To help me complete life well, it’s important to honor my personhood when making medical or care decisions; please don’t talk about me as though I am not still here. I respond best to familiar voices and gentle rhythmic movements. I am ruled by reflexes and will startle easily. My brain is losing its ability to control and heal my body. Be prepared to see me having difficulty breathing or swallowing. My body may no longer desire food and drink as I prepare to leave this life. I may not be able to stop living without permission from you. Your greatest gift at this time in my life is to let me know that it is okay to go.

Target Market(s)

Children of seniors, seniors , rehabilitation centers

Requirements
Must have
• Nice photos of Seniors that are happy doing thing they like to do with help (Caregivers)
• Upbeat . Positive
Nice to have
• Processional looking - but very personal, we are taking care of their love ones
Should not have
• Not to feel like a cold hospital or end of life

```html
<!DOCTYPE html>
<html lang="en">
<head>
<meta charset="utf-8">
<title>Brightwell Hearth Partners – Tri-fold Brochure</title>
<link rel="stylesheet" href="https://fonts.googleapis.com/css2?family=Lora:ital,wght@0,400;0,600;1,500;1,600&family=Oswald:wght@500&family=Roboto:wght@400;700&family=Roboto+Condensed:wght@400;500&display=swap">
<style>
  :root{
    --navy:#2a2766;
    --navy-light:#3d3c8c;
    --stripe:#1b84bd;
    --heading-blue:#1c5f95;
    --sky:#8fd0f5;
    --ink:#2c2c2c;
    --white:#ffffff;
    --backdrop:#e7e4df;
  }
  *{box-sizing:border-box;margin:0;padding:0}
  html,body{width:1200px;height:902px;overflow:hidden;background:var(--backdrop)}
  .brochure{position:absolute;left:20px;top:0;width:1160px;height:902px;overflow:hidden;font-family:"Roboto",Arial,sans-serif;color:var(--ink)}
  .backdrop-shapes{position:absolute;inset:0}
  .script-heading{font-family:"Lora",Georgia,serif;font-style:italic;font-weight:600;color:var(--heading-blue)}

  /* left panel */
  .story{position:absolute;left:30px;top:22px;width:340px}
  .story h2{font-size:24px;margin-bottom:6px}
  .story p{font-size:10.3px;line-height:15px;text-align:justify;hyphens:auto}
  .signature{position:absolute;left:30px;top:404px;font-size:11px;font-weight:700;color:var(--heading-blue)}
  .signature span{font-weight:400}
  .services{position:absolute;left:30px;top:436px;width:340px}
  .services h2{font-size:24px;margin-bottom:4px}
  .service-cols{display:flex;gap:0}
  .service-col{width:174px}
  .service-col h3{font-family:"Roboto Condensed",Arial,sans-serif;font-weight:500;font-size:10.4px;color:var(--heading-blue);margin-bottom:6px;text-transform:uppercase}
  .service-col ul{list-style:none}
  .service-col li{display:flex;align-items:center;gap:6px;font-family:"Roboto Condensed",Arial,sans-serif;font-size:10.4px;height:17px}
  .tick{width:12px;height:12px;flex:none}
  .about-badge{position:absolute;left:126px;top:647px;width:82px;height:82px;border-radius:50%;background:var(--white);border:4px solid #cfd6de;box-shadow:0 0 0 2px var(--navy)}
  .about-badge::after{content:"";position:absolute;inset:10px;border-radius:50%;background:radial-gradient(circle,#6aa9c9,#2f6f97)}
  .about-owner{position:absolute;left:232px;top:685px;font-size:17px;color:var(--white)}
  .about-text{position:absolute;left:30px;top:733px;width:335px;font-size:11.6px;line-height:15.6px;font-weight:700;color:var(--white)}

  /* middle panel */
  .commitment-title{position:absolute;left:383px;top:36px;width:382px;text-align:center;color:var(--white);font-size:25px;line-height:31px;letter-spacing:.5px}
  .commitment{position:absolute;left:400px;width:262px;color:var(--white)}
  .commitment h3{font-family:"Roboto Condensed",Arial,sans-serif;font-weight:400;font-size:15.5px;color:var(--sky);margin-bottom:9px}
  .commitment p{font-size:10.6px;line-height:14.6px}
  .c1{top:193px}.c2{top:312px}.c3{top:411px}.c4{top:512px}
  .photo-dot{position:absolute;width:70px;height:70px;border-radius:50%;border:3px solid var(--white)}
  .badge-dot{background:var(--white);border:4px solid #cfd6de}
  .badge-dot::after{content:"";position:absolute;inset:10px;border-radius:50%;background:radial-gradient(circle,#6aa9c9,#2f6f97)}
  .name-seal{position:absolute;left:474px;top:642px;width:198px;height:68px;border-radius:50%;background:var(--white);border:2px solid var(--stripe);display:flex;align-items:center;justify-content:center;text-align:center;font-family:"Lora",Georgia,serif;font-size:15px;line-height:17px;color:var(--heading-blue)}
  .contact{position:absolute;left:383px;width:382px;display:flex;justify-content:center;align-items:center;gap:8px;color:var(--white);font-weight:700}
  .contact-phone{top:727px;font-size:33px}
  .contact-phone svg{width:32px;height:32px}
  .contact-address{top:774px;font-size:17px;flex-direction:column;gap:2px}
  .contact-address .line{display:flex;align-items:center;gap:8px}
  .contact-web{top:819px;font-size:16.5px}
  .contact svg{width:18px;height:18px;flex:none}

  /* right panel */
  .brand-name{position:absolute;left:765px;top:28px;width:395px;text-align:center;font-family:"Lora",Georgia,serif;font-weight:400;font-size:46px;line-height:46px;color:var(--heading-blue)}
  .tagline{position:absolute;left:765px;top:704px;width:395px;text-align:center;color:var(--white);font-family:"Oswald",Impact,sans-serif;font-weight:500;text-transform:uppercase}
  .tagline .small{display:block;font-size:26px;line-height:32px;letter-spacing:.3px}
  .tagline .large{display:block;font-size:45px;line-height:56px}
  .what-we-do{position:absolute;left:775px;top:810px;width:375px;text-align:center;color:var(--white);font-family:"Lora",Georgia,serif;font-style:italic;font-weight:500;font-size:18px;line-height:22px}
</style>
</head>
<body>
<main class="brochure">
  <svg class="backdrop-shapes" viewBox="0 0 1160 902" width="1160" height="902" aria-hidden="true">
    <defs>
      <linearGradient id="content-glow" x1="0" y1="0" x2="0" y2="1">
        <stop offset="0" stop-color="#46469a"/>
        <stop offset="1" stop-color="#2e2c74"/>
      </linearGradient>
    </defs>
    <rect width="1160" height="902" fill="var(--navy)"/>
    <rect width="383" height="902" fill="var(--white)"/>
    <rect x="383" y="140" width="382" height="540" fill="url(#content-glow)"/>
    <path d="M383,0 H765 V215 C650,130 520,132 383,160 Z" fill="var(--navy)"/>
    <path d="M383,166 C520,140 650,138 765,212" fill="none" stroke="var(--stripe)" stroke-width="6"/>
    <path d="M383,176 C520,150 650,150 765,222" fill="none" stroke="var(--white)" stroke-width="2" opacity=".6"/>
    <path d="M665,0 H1160 V215 C1000,268 870,258 765,205 C720,170 685,95 665,0 Z" fill="var(--white)"/>
    <path d="M765,205 C870,258 1000,268 1160,215 V255 C1000,305 870,298 765,252 Z" fill="var(--navy)"/>
    <path d="M765,256 C870,302 1000,310 1160,260" fill="none" stroke="var(--stripe)" stroke-width="6"/>
    <path d="M0,690 C120,660 260,640 383,636 C520,630 640,652 765,662 C900,672 1050,656 1160,630" fill="none" stroke="var(--stripe)" stroke-width="8"/>
    <path d="M0,702 C120,672 260,652 383,648 C520,642 640,664 765,674 C900,684 1050,668 1160,642 V902 H0 Z" fill="var(--navy)"/>
  </svg>

  <!-- left panel -->
  <section class="story">
    <h2 class="script-heading">Our story:</h2>
    <p>Opening Brightwell Hearth Partners, Inc. is my way of making a difference in an industry that is dominated by franchises that often have their policies dictated by corporate policy-makers who are unfamiliar with local customs. My goal is to raise the level of non-medical home health care in our area by providing additional, customized training, higher wages for our care-partners and an inclusive workforce in the decision-making process when developing customized care planning for our clients. Through collaboration with the client, their family and care-partners I have learned what issues, concerns and disappointments may arise which enables me to provide a more defined solution for those in need. My goal of providing superior training required locating a nationally recognized curriculum that would serve our clients’ needs. I found the perfect fit with Norla Vance’s, Kindred Pathway Method™ and her Shifting Stones Series™. These programs provide our care-partners with the tools needed to handle the challenges of natural aging and living with Dementia. I was so impressed with these programs, I became a Certified Independent Trainer; one of five in the State of Maryland. There is a bonus for our care-partners who are required to maintain Continuing Education Units - these programs qualify for credit! Improving our industry by providing exemplary care-partners is my goal! I look forward to assisting you with your needs!!</p>
  </section>
  <p class="signature">DANA PREWITT, <span>Owner</span></p>

  <section class="services">
    <h2 class="script-heading">Services :</h2>
    <div class="service-cols">
      <div class="service-col">
        <h3>Companion Care Service</h3>
        <ul>
          <li><svg class="tick" viewBox="0 0 12 12"><circle cx="6" cy="6" r="5" fill="none" stroke="#333" stroke-width="1.2"/><path d="M3.3,6 L5.4,8 L10.5,2.2" fill="none" stroke="#333" stroke-width="1.6"/></svg>Conversation &amp; Companionship</li>
          <li><svg class="tick" viewBox="0 0 12 12"><circle cx="6" cy="6" r="5" fill="none" stroke="#333" stroke-width="1.2"/><path d="M3.3,6 L5.4,8 L10.5,2.2" fill="none" stroke="#333" stroke-width="1.6"/></svg>Meal Preparation</li>
          <li><svg class="tick" viewBox="0 0 12 12"><circle cx="6" cy="6" r="5" fill="none" stroke="#333" stroke-width="1.2"/><path d="M3.3,6 L5.4,8 L10.5,2.2" fill="none" stroke="#333" stroke-width="1.6"/></svg>Light House Keeping</li>
          <li><svg class="tick" viewBox="0 0 12 12"><circle cx="6" cy="6" r="5" fill="none" stroke="#333" stroke-width="1.2"/><path d="M3.3,6 L5.4,8 L10.5,2.2" fill="none" stroke="#333" stroke-width="1.6"/></svg>Errand Service</li>
          <li><svg class="tick" viewBox="0 0 12 12"><circle cx="6" cy="6" r="5" fill="none" stroke="#333" stroke-width="1.2"/><path d="M3.3,6 L5.4,8 L10.5,2.2" fill="none" stroke="#333" stroke-width="1.6"/></svg>Grocery Shopping</li>
          <li><svg class="tick" viewBox="0 0 12 12"><circle cx="6" cy="6" r="5" fill="none" stroke="#333" stroke-width="1.2"/><path d="M3.3,6 L5.4,8 L10.5,2.2" fill="none" stroke="#333" stroke-width="1.6"/></svg>Incidental Transportation</li>
          <li><svg class="tick" viewBox="0 0 12 12"><circle cx="6" cy="6" r="5" fill="none" stroke="#333" stroke-width="1.2"/><path d="M3.3,6 L5.4,8 L10.5,2.2" fill="none" stroke="#333" stroke-width="1.6"/></svg>Laundry &amp; Linen Washing</li>
          <li><svg class="tick" viewBox="0 0 12 12"><circle cx="6" cy="6" r="5" fill="none" stroke="#333" stroke-width="1.2"/><path d="M3.3,6 L5.4,8 L10.5,2.2" fill="none" stroke="#333" stroke-width="1.6"/></svg>Medication Reminders</li>
          <li><svg class="tick" viewBox="0 0 12 12"><circle cx="6" cy="6" r="5" fill="none" stroke="#333" stroke-width="1.2"/><path d="M3.3,6 L5.4,8 L10.5,2.2" fill="none" stroke="#333" stroke-width="1.6"/></svg>Recreational Activities</li>
        </ul>
      </div>
      <div class="service-col">
        <h3>Personal Care Services</h3>
        <ul>
          <li><svg class="tick" viewBox="0 0 12 12"><circle cx="6" cy="6" r="5" fill="none" stroke="#333" stroke-width="1.2"/><path d="M3.3,6 L5.4,8 L10.5,2.2" fill="none" stroke="#333" stroke-width="1.6"/></svg>Bathing</li>
          <li><svg class="tick" viewBox="0 0 12 12"><circle cx="6" cy="6" r="5" fill="none" stroke="#333" stroke-width="1.2"/><path d="M3.3,6 L5.4,8 L10.5,2.2" fill="none" stroke="#333" stroke-width="1.6"/></svg>Mobility</li>
          <li><svg class="tick" viewBox="0 0 12 12"><circle cx="6" cy="6" r="5" fill="none" stroke="#333" stroke-width="1.2"/><path d="M3.3,6 L5.4,8 L10.5,2.2" fill="none" stroke="#333" stroke-width="1.6"/></svg>Transferring &amp; Positioning</li>
          <li><svg class="tick" viewBox="0 0 12 12"><circle cx="6" cy="6" r="5" fill="none" stroke="#333" stroke-width="1.2"/><path d="M3.3,6 L5.4,8 L10.5,2.2" fill="none" stroke="#333" stroke-width="1.6"/></svg>Incontinence Care</li>
          <li><svg class="tick" viewBox="0 0 12 12"><circle cx="6" cy="6" r="5" fill="none" stroke="#333" stroke-width="1.2"/><path d="M3.3,6 L5.4,8 L10.5,2.2" fill="none" stroke="#333" stroke-width="1.6"/></svg>Oral Hygiene</li>
          <li><svg class="tick" viewBox="0 0 12 12"><circle cx="6" cy="6" r="5" fill="none" stroke="#333" stroke-width="1.2"/><path d="M3.3,6 L5.4,8 L10.5,2.2" fill="none" stroke="#333" stroke-width="1.6"/></svg>Feeding</li>
          <li><svg class="tick" viewBox="0 0 12 12"><circle cx="6" cy="6" r="5" fill="none" stroke="#333" stroke-width="1.2"/><path d="M3.3,6 L5.4,8 L10.5,2.2" fill="none" stroke="#333" stroke-width="1.6"/></svg>Toileting</li>
          <li><svg class="tick" viewBox="0 0 12 12"><circle cx="6" cy="6" r="5" fill="none" stroke="#333" stroke-width="1.2"/><path d="M3.3,6 L5.4,8 L10.5,2.2" fill="none" stroke="#333" stroke-width="1.6"/></svg>Grooming &amp; Dressing</li>
          <li><svg class="tick" viewBox="0 0 12 12"><circle cx="6" cy="6" r="5" fill="none" stroke="#333" stroke-width="1.2"/><path d="M3.3,6 L5.4,8 L10.5,2.2" fill="none" stroke="#333" stroke-width="1.6"/></svg>Special Diet Preparation</li>
        </ul>
      </div>
    </div>
  </section>

  <div class="about-badge" role="img" aria-label="Certified trainer badge"></div>
  <h2 class="about-owner script-heading" style="color:var(--white)">About owner:</h2>
  <p class="about-text">Dana Prewitt, owner of Brightwell Hearth Partners, has earned her certification as an Independent Trainer in the Kindred Pathway Method (KPM) by Norla Vance, a nationally recognized instructor on natural aging and aging with Dementia. Dana is one of five certified independent trainers in the state of Maryland. All staff will have eight hours of hands on Dementia Kindred Pathway Method training.</p>

  <!-- middle panel -->
  <h2 class="commitment-title script-heading" style="color:var(--white)">Our Commitment<br>to You:</h2>

  <article class="commitment c1">
    <h3>Extensive Care-Partner Education</h3>
    <p>We provide, in addition to state mandated training, eight additional hours of hands-on Dementia training from a Certified, Independent Instructor on the “Kindred Pathway Method” by Norla Vance, a nationally recognized instructor on aging.</p>
  </article>
  <article class="commitment c2">
    <h3>Nutrition/Local Chef Inspired Training</h3>
    <p>We provide six, two-hour food preparation sessions for our care-partners using local chefs, their recipes and locally grown food.</p>
  </article>
  <article class="commitment c3">
    <h3>Meaningful &amp; Engaging Activities</h3>
    <p>We provide a monthly list with local activities to our care-partners based on our client’s interest and capabilities. Focusing on what our client loved to do in the past.</p>
  </article>
  <article class="commitment c4">
    <h3>Home Solutions When Needed</h3>
    <p>We provide management services to help keep our clients in their homes by working with current contractors or locating new ones to properly maintain a safe-living environment.</p>
  </article>

  <div class="photo-dot badge-dot" role="img" aria-label="Certified trainer badge" style="left:670px;top:231px"></div>
  <div class="photo-dot" role="img" aria-label="Photo of fresh fruit, vegetables and juices" style="left:670px;top:309px;background:radial-gradient(circle at 40% 40%,#e9a23b,#b8362a 55%,#5f8a2e)"></div>
  <div class="photo-dot" role="img" aria-label="Photo of a senior man enjoying a hobby at a table" style="left:670px;top:423px;background:radial-gradient(circle at 50% 40%,#f3f1ee,#bfc6cf 60%,#6e7f93)"></div>
  <div class="photo-dot" role="img" aria-label="Photo of a contractor's hard hat and work tools" style="left:670px;top:528px;background:radial-gradient(circle at 40% 35%,#f2c230,#c98a1f 55%,#6b5a45)"></div>

  <div class="name-seal">Brightwell<br>Hearth Partners</div>

  <p class="contact contact-phone">
    <svg viewBox="0 0 32 32" aria-hidden="true"><circle cx="16" cy="16" r="14" fill="none" stroke="#fff" stroke-width="2.2"/><path d="M11,9 c-1.5,1 -2,3 -1,5.5 c1.5,3.6 4.5,7 8.5,8.5 c2.4,1 4.2,0.3 5.2,-1.2 l-3,-3 l-2.3,1.2 c-2,-1 -3.6,-2.7 -4.6,-4.6 l1.2,-2.3 Z" fill="#fff"/></svg>
    410-555-0148
  </p>
  <div class="contact contact-address">
    <span class="line"><svg viewBox="0 0 18 18" aria-hidden="true"><path d="M9,1.5 a5,5 0 0 1 5,5 c0,3.8 -5,10 -5,10 s-5,-6.2 -5,-10 a5,5 0 0 1 5,-5 Z" fill="#7cc6f0"/><circle cx="9" cy="6.5" r="2" fill="var(--navy)"/></svg>318 Corvane Street</span>
    <span class="line">Easton, MD 21774</span>
  </div>
  <p class="contact contact-web">
    <svg viewBox="0 0 18 18" aria-hidden="true"><g fill="none" stroke="#7cc6f0" stroke-width="1.4"><circle cx="9" cy="9" r="7.5"/><ellipse cx="9" cy="9" rx="3.3" ry="7.5"/><path d="M1.5,9 H16.5 M3,5 H15 M3,13 H15"/></g></svg>
    BrightwellHearthPartners.example
  </p>

  <!-- right panel -->
  <h1 class="brand-name">Brightwell<br>Hearth<br>Partners</h1>

  <div role="img" aria-label="Photo of a smiling young caregiver with her hand on the shoulder of a happy senior man at home" style="position:absolute;left:765px;top:250px;width:395px;height:420px;background:linear-gradient(100deg,#e9eef0 0%,#f4efe9 30%,#d8c2a6 60%,#b7956f 85%,#c9b9a4 100%);z-index:-0"></div>
  <svg viewBox="0 0 395 60" width="395" height="60" aria-hidden="true" style="position:absolute;left:765px;top:240px">
    <path d="M0,12 C105,58 235,66 395,16 V0 H0 Z" fill="var(--navy)"/>
    <path d="M0,16 C105,62 235,70 395,20" fill="none" stroke="var(--stripe)" stroke-width="6"/>
  </svg>
  <svg viewBox="0 0 395 60" width="395" height="60" aria-hidden="true" style="position:absolute;left:765px;top:628px">
    <path d="M0,34 C135,44 285,28 395,2" fill="none" stroke="var(--stripe)" stroke-width="8"/>
    <path d="M0,46 C135,56 285,40 395,14 V60 H0 Z" fill="var(--navy)"/>
  </svg>

  <p class="tagline"><span class="small">Devoted to Thoughtful</span><span class="large">Household Support</span></p>
  <p class="what-we-do">Home care agency that services higher end Clients. Taking care of seniors in their home.</p>
</main>
</body>
</html>
```